Business Card Design

We are a commercial real estate brokerage in San Francisco, leasing office buildings downtown.
I would like a clean, elegant look. Simple but powerful .

Industry/Entity Type

Business

Contact Information for Business Card

Derek Holloway
lic# 07258143
415.555.0172
derek@velt-commercial.example
velt-commercial.example

```html
<!DOCTYPE html>
<html lang="en">
<head>
<meta charset="utf-8">
<title>Velt Commercial – Business Card</title>
<link rel="stylesheet" href="https://fonts.googleapis.com/css2?family=Source+Sans+3:ital,wght@0,400;0,700;1,400&display=swap">
<style>
  :root {
    --page-bg: #efefed;
    --card-top: #e3e6ea;
    --card-top-edge: #d5d9df;
    --band-dark: #1f2125;
    --band-dark-2: #2c2f35;
    --strip-top: #59606c;
    --strip-bottom: #8d95a3;
    --brand-ink: #2e3a4b;
    --name-ink: #7d8eac;
    --lic-ink: #d4d4d6;
    --contact-ink: #cdb29c;
    --icon-ink: #8c95a6;
    --tag-ink-1: #caa18c;
    --tag-ink-2: #e2d5c8;
  }
  * { box-sizing: border-box; margin: 0; padding: 0; }
  html, body {
    width: 1200px; height: 969px; overflow: hidden;
    background: var(--page-bg);
    font-family: "Source Sans 3", sans-serif;
  }
  .card {
    position: absolute; left: 100px; top: 200px;
    width: 1000px; height: 569px;
    border-radius: 6px; overflow: hidden;
    background: linear-gradient(180deg, var(--card-top) 0%, var(--card-top-edge) 100%);
    box-shadow: 0 10px 30px rgba(0,0,0,0.12);
  }
  .brand {
    position: absolute; left: 0; right: 0; top: 108px;
    text-align: center;
    font-size: 60px; font-weight: 700; letter-spacing: 2px;
    color: var(--brand-ink);
  }
  .contact-band {
    position: absolute; left: 0; top: 294px; width: 100%; height: 172px;
    background: linear-gradient(180deg, var(--band-dark-2) 0%, var(--band-dark) 100%);
  }
  .holder {
    position: absolute; right: 601px; top: 44px; text-align: right;
  }
  .holder-name { font-size: 33px; color: var(--name-ink); line-height: 1.1; }
  .holder-license { font-size: 26px; color: var(--lic-ink); margin-top: 6px; }
  .contact-list {
    position: absolute; left: 440px; top: 30px; list-style: none;
  }
  .contact-list li {
    display: flex; align-items: center; height: 38px;
    font-size: 25px; color: var(--contact-ink);
  }
  .contact-list svg { width: 24px; height: 24px; margin-right: 20px; fill: var(--icon-ink); }
  .tagline-strip {
    position: absolute; left: 0; top: 466px; width: 100%; height: 103px;
    background: linear-gradient(180deg, var(--strip-top) 0%, var(--strip-bottom) 100%);
    text-align: center; font-style: italic; font-size: 25px; line-height: 34px;
    padding-top: 16px;
  }
  .tagline-strip .line-one { color: var(--tag-ink-1); }
  .tagline-strip .line-two { color: var(--tag-ink-2); }
</style>
</head>
<body>
  <div class="card">
    <div class="brand">VELT COMMERCIAL</div>

    <div class="contact-band">
      <div class="holder">
        <div class="holder-name">Derek Holloway</div>
        <div class="holder-license">lic# 07258143</div>
      </div>
      <ul class="contact-list">
        <li>
          <svg viewBox="0 0 24 24" aria-hidden="true"><path d="M6.6 10.8a15.1 15.1 0 0 0 6.6 6.6l2.2-2.2a1 1 0 0 1 1-.25 11.4 11.4 0 0 0 3.6.57 1 1 0 0 1 1 1V20a1 1 0 0 1-1 1A17 17 0 0 1 3 4a1 1 0 0 1 1-1h3.5a1 1 0 0 1 1 1c0 1.25.2 2.45.57 3.57a1 1 0 0 1-.25 1z"/></svg>
          415.555.0172
        </li>
        <li>
          <svg viewBox="0 0 24 24" aria-hidden="true"><path d="M2 5h20v14H2z M3 6l9 7 9-7" fill="none" stroke="var(--icon-ink)" stroke-width="0"/><path d="M2 5h20v2l-10 7L2 7z"/><path d="M2 9l10 7 10-7v10H2z"/></svg>
          derek@velt-commercial.example
        </li>
        <li>
          <svg viewBox="0 0 24 24" aria-hidden="true"><circle cx="12" cy="12" r="10"/><path d="M7 8c2 0 3 1 3 3s-2 2-2 4 1 3 1 4M15 5c-1 2 0 3 2 3s3 2 2 4" fill="none" stroke="var(--band-dark)" stroke-width="1.6"/></svg>
          velt-commercial.example
        </li>
      </ul>
    </div>

    <div class="tagline-strip">
      <div class="line-one">commercial real estate brokerage in San Francisco</div>
      <div class="line-two">leasing office buildings downtown.</div>
    </div>
  </div>
</body>
</html>
```